MALT CALEDON/BRACKENRIDGE DISTILLERY

DOUBLE SIDED BUSINESS CARD ONE SIDE FOR WWW.MALTCALEDON.ORG AND ONE SIDE FOR BRACKENRIDGE DISTILLERY ARTWORK FOR WEBSITE IS ATTACHED

1)
GORDON PRITCHARD CEO
MALT CALEDON
Office 1 Harbourgate House
14 Fernbrook Place
Glasgow
Scotland, G5 2QT
W:WWW.MALTCALEDON.ORG
E:GORDON@MALTCALEDON.ORG
T:+44 7491 355018

2)
GORDON PRITCHARD CEO
BRACKENRIDGE DISTILLERY
Building 418, Hangarpark Oosterhof,
3e Brinkweg, Katwijk, 2226KM

W: WWW.brackenridgedistillery.nl
E: GORDON@brackenridgedistillery.nl
T:+44 7491 355018

1)
Marit Steenbergen DIRECTOR
MALT CALEDON
Office 1 Harbourgate House
14 Fernbrook Place
Glasgow
Scotland, G5 2QT
W:WWW.MALTCALEDON.ORG
E:Marit@MALTCALEDON.ORG
T:+31 6 58193047

2)
MARIT STEENBERGEN DIRECTOR
BRACKENRIDGE DISTILLERY

E: marit@brackenridgedistillery.nl
T:+31 6 58193047

```html
<!DOCTYPE html>
<html lang="en">
<head>
<meta charset="utf-8">
<title>Malt Caledon / Brackenridge Distillery — Business Card</title>
<link href="https://fonts.googleapis.com/css2?family=Montserrat:wght@500;700;800&family=Arimo:ital,wght@0,400;0,700;1,400&display=swap" rel="stylesheet">
<style>
  :root{
    --page:#2a2a2a;
    --paper:#f7f6f3;
    --ink-dark:#161211;
    --slate:#3b3b3c;
    --gold:#c3982e;
    --gold-light:#e0bd58;
    --gold-deep:#8a6a22;
    --white:#ffffff;
    --text-dark:#2b2b2b;
  }
  *{box-sizing:border-box;margin:0;padding:0}
  html,body{width:1200px;height:963px;overflow:hidden;background:var(--page)}
  .canvas{position:relative;width:1200px;height:963px}
  .card{position:absolute;left:268px;width:664px;height:410px;overflow:hidden;box-shadow:0 8px 24px rgba(0,0,0,.45)}
  .card--front{top:48px;background:var(--paper)}
  .card--back{top:505px;background:var(--ink-dark)}
  .card__shapes{position:absolute;inset:0}

  .wordmark{position:absolute;font-family:"Montserrat",sans-serif;font-weight:700;letter-spacing:.06em;white-space:nowrap;z-index:2}
  .card--front .wordmark{left:250px;top:52px;font-size:40px;color:var(--gold)}
  .card--back .wordmark{right:34px;top:40px;font-size:28px;color:var(--white);text-align:right;line-height:1.15}

  .person{position:absolute;left:56px;top:150px;z-index:2}
  .card--back .person{left:40px;top:128px}
  .person__name{font-family:"Montserrat",sans-serif;font-weight:800;font-size:20px;color:var(--gold);letter-spacing:.01em}
  .person__role{font-family:"Arimo",sans-serif;font-size:13px;color:var(--text-dark);margin-top:1px}
  .card--back .person__role{color:var(--white)}

  .contacts{list-style:none;margin-top:16px;font-family:"Arimo",sans-serif;font-size:13px;color:var(--text-dark)}
  .card--back .contacts{color:var(--white)}
  .contacts li{display:flex;align-items:center;gap:8px;height:20px}
  .contacts svg{width:13px;height:13px;flex:none}

  .address{position:absolute;font-family:"Arimo",sans-serif;font-size:14px;line-height:1.45;color:var(--white);z-index:2}
  .card--front .address{left:40px;top:326px}
  .card--back .address{left:40px;top:318px}

  .artwork{position:absolute;z-index:1}
  .artwork--stag{left:410px;top:150px;width:240px;height:260px;border-radius:48% 48% 0 0;background:radial-gradient(ellipse at 55% 55%,var(--gold-light),var(--gold) 60%,var(--gold-deep))}
  .artwork--skyline{left:430px;top:150px;width:170px;height:260px;background:linear-gradient(160deg,var(--gold-deep),var(--gold-light) 55%,var(--gold))}
</style>
</head>
<body>
<main class="canvas">

  <section class="card card--front" aria-label="Malt Caledon side">
    <svg class="card__shapes" viewBox="0 0 664 410" preserveAspectRatio="none" aria-hidden="true">
      <polygon points="0,300 430,300 400,410 0,410" fill="var(--slate)"/>
      <defs><linearGradient id="goldBandFront" x1="0" x2="1"><stop offset="0" stop-color="var(--gold-deep)"/><stop offset=".5" stop-color="var(--gold-light)"/><stop offset="1" stop-color="var(--gold)"/></linearGradient></defs>
      <rect x="470" y="340" width="194" height="70" fill="url(#goldBandFront)"/>
    </svg>

    <div class="wordmark">MALT CALEDON</div>

    <div class="person">
      <div class="person__name">GORDON PRITCHARD</div>
      <div class="person__role">CEO</div>
      <ul class="contacts">
        <li><svg viewBox="0 0 16 16"><circle cx="8" cy="8" r="8" fill="var(--gold)"/><path d="M5 4.5l1.6-.4 1 2-1 .8a5 5 0 002.5 2.5l.8-1 2 1-.4 1.6C8 11.5 4.5 8 5 4.5z" fill="var(--white)"/></svg>+44 7491 355018</li>
        <li><svg viewBox="0 0 16 16"><rect x="1" y="3" width="14" height="10" fill="var(--gold)"/><path d="M1 3l7 6 7-6" stroke="var(--white)" fill="none" stroke-width="1.3"/></svg>GORDON@MALTCALEDON.ORG</li>
        <li><svg viewBox="0 0 16 16"><circle cx="8" cy="8" r="7" fill="var(--gold)"/><path d="M1 8h14M8 1c-3 3-3 11 0 14M8 1c3 3 3 11 0 14" stroke="var(--white)" fill="none" stroke-width="1"/></svg>WWW.MALTCALEDON.ORG</li>
      </ul>
    </div>

    <div class="address">Office 1 Harbourgate House<br>14 Fernbrook Place, Glasgow, Scotland, G5 2QT</div>

    <div class="artwork artwork--stag" role="img" aria-label="Gold stag head illustration with large antlers"></div>
  </section>

  <section class="card card--back" aria-label="Brackenridge Distillery side">
    <svg class="card__shapes" viewBox="0 0 664 410" preserveAspectRatio="none" aria-hidden="true">
      <defs><linearGradient id="goldBandBack" x1="0" x2="1"><stop offset="0" stop-color="var(--gold-deep)"/><stop offset=".6" stop-color="var(--gold)"/><stop offset="1" stop-color="var(--gold-light)"/></linearGradient></defs>
      <polygon points="0,295 500,295 470,410 0,410" fill="url(#goldBandBack)"/>
      <rect x="600" y="372" width="50" height="38" fill="var(--white)"/>
    </svg>

    <div class="wordmark">BRACKENRIDGE<br>DISTILLERY</div>

    <div class="person">
      <div class="person__name">GORDON PRITCHARD</div>
      <div class="person__role">CEO</div>
      <ul class="contacts">
        <li><svg viewBox="0 0 16 16"><circle cx="8" cy="8" r="8" fill="var(--gold)"/><path d="M5 4.5l1.6-.4 1 2-1 .8a5 5 0 002.5 2.5l.8-1 2 1-.4 1.6C8 11.5 4.5 8 5 4.5z" fill="var(--ink-dark)"/></svg>+44 7491 355018</li>
        <li><svg viewBox="0 0 16 16"><rect x="1" y="3" width="14" height="10" fill="var(--gold)"/><path d="M1 3l7 6 7-6" stroke="var(--ink-dark)" fill="none" stroke-width="1.3"/></svg>GORDON@brackenridgedistillery.nl</li>
        <li><svg viewBox="0 0 16 16"><circle cx="8" cy="8" r="7" fill="var(--gold)"/><path d="M1 8h14M8 1c-3 3-3 11 0 14M8 1c3 3 3 11 0 14" stroke="var(--ink-dark)" fill="none" stroke-width="1"/></svg>WWW.brackenridgedistillery.nl</li>
      </ul>
    </div>

    <div class="address">Building 418, Hangarpark Oosterhof,<br>3e Brinkweg, Katwijk, 2226KM</div>

    <div class="artwork artwork--skyline" role="img" aria-label="Gold outlined distillery building illustration"></div>
  </section>

</main>
</body>
</html>
```